Thornbury Building Company - Card Design

I am looking to use the logo designs that you already did for me to develop a business card. I would like the card to have a black background and be double sided. I want white and green logo and text. I have attached an inspiration photo of a look that I like. I would like to use the Vertical Logo attached to take up the full front side of the card. On the back where I have my name and information, I would like to have the horizontal logo or maybe even just the image of the 'A' and trees without the text. I am open, but I am looking for something clean and simple and I want the green to really pop! Additional files can be found under Design #: 58302946

Target Market(s)

Homeowners

Industry/Entity Type

Construction

Contact Information for Business Card

Name: Marcus Thornbury, Title: Project Manager, Phone: 555.274.8136, Email: thornburybuildingcompany@mailvesta.com, address: 487 Larkspur Ln, Felton, CA 95033, Lic# 2468317

Colors
00AB8E
00BBA5
67D7C9
C6EFE9
E9F9F6

Requirements
Nice to have
• I would like to see the logos that I have already got from ArtLoomHub, though I am open to new ones

```html
<!DOCTYPE html>
<html lang="en">
<head>
<meta charset="utf-8">
<title>Thornbury Building Company – Business Card</title>
<link rel="stylesheet" href="https://fonts.googleapis.com/css2?family=Arimo:wght@400;700&display=swap">
<style>
  :root {
    --page-bg: #e4e4e2;
    --card-white: #ffffff;
    --card-dark: #2b2b2b;
    --card-dark-deep: #181818;
    --card-dark-mid: #262626;
    --card-dark-soft: #4d4d4d;
    --brand-green: #3bb54a;
    --text-grey: #6a6a6a;
    --text-white: #ffffff;
  }
  * { box-sizing: border-box; margin: 0; padding: 0; }
  html, body { width: 1200px; height: 801px; overflow: hidden; }
  body {
    background: var(--page-bg);
    font-family: "Arimo", Arial, sans-serif;
    position: relative;
  }
  .card {
    position: absolute;
    top: 246px;
    width: 540px;
    height: 309px;
    border-radius: 3px;
    overflow: hidden;
    box-shadow: 0 8px 24px rgba(0,0,0,0.18);
  }
  .card--info { left: 40px; background: var(--card-white); }
  .card--brand { left: 620px; background: var(--card-dark); }

  /* Contact side */
  .brand-lockup {
    position: absolute;
    left: 40px;
    top: 104px;
    width: 170px;
    display: flex;
    align-items: center;
    gap: 12px;
  }
  .brand-lockup__square {
    flex: none;
    width: 22px;
    height: 22px;
    background: var(--brand-green);
  }
  .brand-lockup__name {
    color: var(--brand-green);
    font-weight: 700;
    font-size: 17px;
    line-height: 1.2;
  }
  .contact {
    position: absolute;
    left: 246px;
    top: 52px;
    right: 20px;
    color: var(--text-grey);
  }
  .contact__name {
    color: var(--brand-green);
    font-weight: 700;
    font-size: 21px;
    line-height: 1.1;
  }
  .contact__title { font-size: 13px; margin-top: 4px; }
  .contact__license { font-size: 13px; margin-top: 3px; }
  .contact__license span { color: var(--brand-green); }
  .contact__lines { list-style: none; margin-top: 20px; font-size: 12.5px; }
  .contact__lines li { display: flex; align-items: center; gap: 8px; margin-top: 5px; }
  .contact__lines svg { flex: none; }
  .contact__address { font-size: 13px; margin-top: 44px; }

  /* Brand side */
  .brand-pattern {
    position: absolute;
    inset: 0;
    background:
      linear-gradient(160deg, rgba(0,0,0,0) 40%, rgba(0,0,0,0.18) 100%),
      linear-gradient(105deg, var(--card-dark-deep) 0%, var(--card-dark-mid) 45%, var(--card-dark) 62%, var(--card-dark-soft) 100%);
  }
  .brand-mark {
    position: absolute;
    left: 190px;
    top: 170px;
    display: flex;
    align-items: center;
    gap: 12px;
  }
  .brand-mark__square {
    flex: none;
    width: 26px;
    height: 26px;
    background: var(--brand-green);
  }
  .brand-mark__name {
    color: var(--text-white);
    font-weight: 700;
    font-size: 19px;
    letter-spacing: 0.5px;
    line-height: 1.2;
    white-space: nowrap;
  }
</style>
</head>
<body>
  <section class="card card--info" aria-label="Business card, contact side">
    <div class="brand-lockup">
      <span class="brand-lockup__square"></span>
      <span class="brand-lockup__name">Thornbury Building Company</span>
    </div>
    <div class="contact">
      <p class="contact__name">Marcus Thornbury</p>
      <p class="contact__title">Project Manager</p>
      <p class="contact__license"><span>Lic#</span> 2468317</p>
      <ul class="contact__lines">
        <li>
          <svg width="11" height="11" viewBox="0 0 24 24" aria-hidden="true"><path fill="var(--brand-green)" d="M6.6 10.8a15.1 15.1 0 0 0 6.6 6.6l2.2-2.2a1 1 0 0 1 1-.25 11.4 11.4 0 0 0 3.6.57 1 1 0 0 1 1 1V20a1 1 0 0 1-1 1A17 17 0 0 1 3 4a1 1 0 0 1 1-1h3.5a1 1 0 0 1 1 1c0 1.25.2 2.45.57 3.57a1 1 0 0 1-.25 1z"/></svg>
          555.274.8136
        </li>
        <li>
          <svg width="11" height="11" viewBox="0 0 24 24" aria-hidden="true"><rect x="2" y="5" width="20" height="14" rx="1" fill="none" stroke="var(--brand-green)" stroke-width="2.4"/><path d="M2 6l10 7 10-7" fill="none" stroke="var(--brand-green)" stroke-width="2.4"/></svg>
          thornburybuildingcompany@mailvesta.com
        </li>
      </ul>
      <p class="contact__address">487 Larkspur Ln, Felton, CA 95033</p>
    </div>
  </section>

  <section class="card card--brand" aria-label="Business card, brand side">
    <div class="brand-pattern" role="img" aria-label="Embossed repeating brand pattern in dark grey tones, darker at left and lighter at right"></div>
    <div class="brand-mark">
      <span class="brand-mark__square"></span>
      <span class="brand-mark__name">Thornbury Building Company</span>
    </div>
  </section>
</body>
</html>
```